Kelo Wave Mint Business cards

Logo, tag line and photo on card
Agent Name
Title
Address
Phone number
Email
Website
Make logo on one side large by rotating  to portrait format.  Keep the background of the logo white.

Contact Information for Business Card
Slogan; Making Every Wave Count

```html
<!DOCTYPE html>
<html lang="en">
<head>
<meta charset="utf-8">
<title>Kelo Wave Mint – Business Cards</title>
<link href="https://fonts.googleapis.com/css2?family=Open+Sans:wght@400;600;700&display=swap" rel="stylesheet">
<style>
  :root {
    --page-bg: #232323;
    --card-bg: #1e1e1f;
    --brand-red: #c8202a;
    --brand-navy: #2a3a80;
    --text-light: #f2f2f2;
    --photo-dark: #2a2a2b;
    --photo-mid: #8a8580;
  }
  * { margin: 0; padding: 0; box-sizing: border-box; }
  html, body { width: 1200px; height: 711px; overflow: hidden; }
  body {
    background: var(--page-bg);
    font-family: "Open Sans", Arial, sans-serif;
    position: relative;
  }
  .card {
    position: absolute;
    top: 190px;
    width: 540px;
    height: 320px;
    background: var(--card-bg);
    border-radius: 22px;
    border-bottom: 4px solid var(--brand-red);
    box-shadow: 0 0 0 1px rgba(200,32,42,.55), 0 14px 30px rgba(0,0,0,.55);
    overflow: hidden;
  }
  .card--front { left: 40px; }
  .card--back { left: 620px; }

  /* Brand name with plain square mark */
  .brand {
    display: flex;
    align-items: center;
    color: var(--text-light);
    font-weight: 700;
    white-space: nowrap;
  }
  .brand-square {
    background: var(--brand-red);
    flex: none;
  }
  .card--front .brand {
    position: absolute;
    left: 0; right: 0;
    top: 112px;
    justify-content: center;
    gap: 16px;
    font-size: 40px;
    line-height: 1;
  }
  .card--front .brand-square { width: 30px; height: 30px; }
  .tagline {
    position: absolute;
    left: 0; right: 0;
    top: 178px;
    text-align: center;
    color: var(--brand-red);
    font-size: 15px;
    font-weight: 600;
  }

  /* Back side */
  .card--back .brand {
    position: absolute;
    left: 26px;
    top: 34px;
    gap: 10px;
    font-size: 22px;
    line-height: 1;
  }
  .card--back .brand-square { width: 16px; height: 16px; }
  .photo {
    position: absolute;
    right: 0;
    top: 0;
    width: 250px;
    height: 100%;
    background: radial-gradient(ellipse at 55% 45%, var(--photo-mid) 0%, #5a5654 35%, var(--photo-dark) 75%, var(--card-bg) 100%);
  }
  .identity {
    position: absolute;
    left: 22px;
    top: 140px;
    padding-left: 12px;
    border-left: 7px solid var(--brand-red);
  }
  .agent-name {
    font-size: 22px;
    font-weight: 700;
    line-height: 1.1;
  }
  .agent-name .first { color: var(--brand-red); }
  .agent-name .last { color: var(--brand-navy); }
  .agent-title {
    color: var(--text-light);
    font-size: 12.5px;
    font-weight: 600;
    margin-top: 2px;
  }
  .address {
    position: absolute;
    left: 48px;
    top: 200px;
    color: var(--text-light);
    font-size: 12px;
    font-style: normal;
    line-height: 1.35;
  }
  .contacts {
    position: absolute;
    left: 30px;
    top: 246px;
    list-style: none;
    color: var(--text-light);
    font-size: 12px;
    line-height: 1.5;
  }
  .contacts li { display: flex; align-items: center; gap: 8px; }
  .contacts svg { width: 12px; height: 12px; fill: var(--brand-red); flex: none; }
</style>
</head>
<body>
  <section class="card card--front">
    <div class="brand"><span class="brand-square"></span><span>Kelo Wave Mint</span></div>
    <p class="tagline">Making Every Wave Count</p>
  </section>

  <section class="card card--back">
    <div class="photo" role="img" aria-label="Portrait photo of the agent"></div>
    <div class="brand"><span class="brand-square"></span><span>Kelo Wave Mint</span></div>
    <div class="identity">
      <h1 class="agent-name"><span class="first">Marta</span> <span class="last">Lindqvist</span></h1>
      <p class="agent-title">Managing Director</p>
    </div>
    <address class="address">
      1480 Cedar Ridge Ave. Suite<br>310 Denton, TX 76201
    </address>
    <ul class="contacts">
      <li>
        <svg viewBox="0 0 24 24" aria-hidden="true"><path d="M6.6 10.8a15.1 15.1 0 0 0 6.6 6.6l2.2-2.2a1 1 0 0 1 1-.25 11.4 11.4 0 0 0 3.6.57 1 1 0 0 1 1 1V20a1 1 0 0 1-1 1A17 17 0 0 1 3 4a1 1 0 0 1 1-1h3.5a1 1 0 0 1 1 1c0 1.25.2 2.45.57 3.57a1 1 0 0 1-.25 1z"/></svg>
        (555) 014-3827
      </li>
      <li>
        <svg viewBox="0 0 24 24" aria-hidden="true"><path d="M3 5h18a1 1 0 0 1 1 1v12a1 1 0 0 1-1 1H3a1 1 0 0 1-1-1V6a1 1 0 0 1 1-1zm9 7 8-5H4z"/></svg>
        info@kelowavemint.com
      </li>
      <li>
        <svg viewBox="0 0 24 24" aria-hidden="true"><path d="M12 2a10 10 0 1 0 0 20 10 10 0 0 0 0-20zm6.9 9h-3a15 15 0 0 0-1.2-5.6A8 8 0 0 1 18.9 11zM12 4.1c.9 1.2 1.8 3.6 1.9 6.9h-3.8c.1-3.3 1-5.7 1.9-6.9zM9.3 5.4A15 15 0 0 0 8.1 11h-3a8 8 0 0 1 4.2-5.6zM5.1 13h3a15 15 0 0 0 1.2 5.6A8 8 0 0 1 5.1 13zm6.9 6.9c-.9-1.2-1.8-3.6-1.9-6.9h3.8c-.1 3.3-1 5.7-1.9 6.9zm2.7-1.3a15 15 0 0 0 1.2-5.6h3a8 8 0 0 1-4.2 5.6z"/></svg>
        www.kelowavemint.com
      </li>
    </ul>
  </section>
</body>
</html>
```